Seeking funky, innovative business cards

I am looking to refresh our current business cards to something more engaging, visual and impactful. We are a management consultancy firm, see website (www.larkstone-partners.com.au). I've included our colour scheme, sample of the slides we use and our old business cards. We would like our cards to have icons. The card should display:- Name- Title- Mobile number- Address- Email address- Website - Company logo- Our purpose statement "we shape workplaces where people love to grow"

Contact Information for Business Card

Brennan Ulfsson
Consultant
0468 927 341
Level 3, 218 Wexley Street, Melbourne 3000
brennan@larkstone-partners.com.au
www.larkstone-partners.com.au

Purpose statement "we shape workplaces where people love to grow"
LOGO available in google images

Font styles to use
Other font styles liked:
• Open Sans Light, Bebas Neue (open to other cool foints)

Colors
ffc214
5c5c5c
f5f5f5
fefefe

Requirements
Must have
• - Name
• - Title
• - Mobile number
• - Address
• - Email address
• - Website
• - Company logo
• - Our purpose statement "we shape workplaces where people love to grow"
Nice to have
• - Icons
• - Colour (see our colour scheme"

```html
<!DOCTYPE html>
<html lang="en">
<head>
<meta charset="utf-8">
<title>Larkstone Partners — Business Card</title>
<link href="https://fonts.googleapis.com/css2?family=Roboto:ital,wght@0,300;0,400;0,500;1,500&display=swap" rel="stylesheet">
<style>
  :root {
    --backdrop: #b4b4b4;
    --card-white: #fefefe;
    --card-dark: #454a4a;
    --ink: #4a4d4d;
    --ink-soft: #555858;
    --accent: #f7a928;
    --accent-yellow: #ffc214;
    --light: #f5f5f5;
  }
  * { margin: 0; padding: 0; box-sizing: border-box; }
  html, body { width: 1200px; height: 1200px; overflow: hidden; }
  body {
    background: var(--backdrop);
    font-family: "Roboto", Arial, sans-serif;
    position: relative;
  }
  .card {
    position: absolute;
    left: 217px;
    width: 800px;
    box-shadow: 1px 2px 3px rgba(0,0,0,0.35);
  }
  .card--front { top: 115px; height: 456px; background: var(--card-white); }
  .card--back  { top: 638px; height: 457px; background: var(--card-dark); }

  .brand {
    position: absolute;
    left: 64px;
    top: 82px;
    display: flex;
    align-items: center;
    gap: 12px;
  }
  .brand__dot {
    width: 14px; height: 14px; border-radius: 50%;
    background: var(--accent-yellow);
  }
  .brand__name {
    font-weight: 300;
    font-size: 58px;
    letter-spacing: -1px;
    color: var(--ink);
    line-height: 1;
  }

  .contact {
    position: absolute;
    right: 59px;
    top: 196px;
    text-align: right;
    color: var(--ink-soft);
  }
  .contact__name {
    font-size: 30px;
    font-weight: 400;
    color: var(--accent);
    line-height: 36px;
  }
  .contact__title {
    font-size: 20px;
    font-weight: 500;
    color: var(--ink);
    line-height: 24px;
  }
  .contact__address {
    margin-top: 15px;
    font-size: 18.5px;
    line-height: 24px;
  }
  .contact__list { list-style: none; margin-top: 14px; }
  .contact__item {
    display: flex;
    justify-content: flex-end;
    align-items: center;
    gap: 16px;
    font-size: 18.5px;
    line-height: 25.5px;
  }
  .contact__item svg { width: 20px; height: 20px; flex: none; }

  .back-brand {
    position: absolute;
    left: 0; right: 0;
    top: 190px;
    display: flex;
    justify-content: center;
    align-items: center;
    gap: 18px;
  }
  .back-brand__dot {
    width: 26px; height: 26px; border-radius: 50%;
    background: var(--accent-yellow);
  }
  .back-brand__name {
    font-weight: 300;
    font-size: 72px;
    color: var(--light);
    letter-spacing: -1px;
    line-height: 1;
  }
  .purpose {
    position: absolute;
    left: 0; right: 0;
    top: 380px;
    text-align: center;
    font-style: italic;
    font-weight: 500;
    font-size: 21px;
    color: var(--light);
  }
  .purpose__accent { color: var(--accent); }
</style>
</head>
<body>
  <section class="card card--front">
    <div class="brand">
      <span class="brand__name">Larkstone</span>
      <span class="brand__dot"></span>
    </div>

    <div class="contact">
      <p class="contact__name">Brennan Ulfsson</p>
      <p class="contact__title">Consultant</p>
      <p class="contact__address">Level 3, 218 Wexley Street,<br>Melbourne 3000</p>
      <ul class="contact__list">
        <li class="contact__item">0468 927 341
          <svg viewBox="0 0 20 20" aria-hidden="true"><path fill="var(--accent)" d="M5 2.5l2.6 3-1.4 2.1c.9 2.1 2.6 3.8 4.6 4.8l2.1-1.4 3 2.6-1.6 2.6C9.4 16.5 3.6 10.8 2.9 4.2z"/></svg>
        </li>
        <li class="contact__item">brennan@larkstone-partners.com.au
          <svg viewBox="0 0 20 20" aria-hidden="true"><rect x="2" y="5" width="16" height="11" fill="var(--accent)"/><path d="M2.5 5.5l7.5 6 7.5-6" fill="none" stroke="#fff" stroke-width="1.3"/></svg>
        </li>
        <li class="contact__item">www.larkstone-partners.com.au
          <svg viewBox="0 0 20 20" aria-hidden="true"><circle cx="10" cy="10" r="8.5" fill="var(--accent)"/><path d="M6 5c2 1 1 3 3 3s1 3 3 3-1 4 1 4M13 4c-1 2 1 3 3 3" fill="none" stroke="#fff" stroke-width="1.4"/></svg>
        </li>
      </ul>
    </div>
  </section>

  <section class="card card--back">
    <div class="back-brand">
      <span class="back-brand__name">Larkstone</span>
      <span class="back-brand__dot"></span>
    </div>
    <p class="purpose">we shape workplaces where <span class="purpose__accent">people love to grow</span></p>
  </section>
</body>
</html>
```